Hello my Name is Elias Moreno. I buy and sell vintage comic books, you can refer to my instragram page qpkz.comics to get ideas and inspiration. For the front of the card I would like my company logo QPKZ Comics with a yellow and black background with the bat signal or bat emblem like on my IG page and with my info Elias Moreno as the Owner and address/ phone number, PO Box 617283, Miami, FL 33827, 305-482-6170 and that I buy and sell comics & collectables . Also feel free to be open to other ideas if you want. Im not stuck on one design. For the back of the card I would like for it to say follow me on Instagram QPKZ.Comics with the ig emblem. Also would like the card to be vertical if possible. Thanks

```html
<!DOCTYPE html>
<html lang="en">
<head>
<meta charset="utf-8">
<title>QPKZ Comics – Business Cards</title>
<link rel="stylesheet" href="https://fonts.googleapis.com/css2?family=Orbitron:wght@700;800&family=Roboto:wght@400;500&display=swap">
<style>
  :root {
    --stage: #1b1d20;
    --yellow: #fcc419;
    --black: #0d0d0d;
    --white: #ffffff;
    --ink: #1a1a1a;
    --display: "Orbitron", sans-serif;
    --body: "Roboto", sans-serif;
  }
  * { box-sizing: border-box; margin: 0; padding: 0; }
  html, body { width: 1200px; height: 987px; overflow: hidden; }
  body { background: var(--stage); position: relative; font-family: var(--body); color: var(--ink); }

  .card {
    position: absolute;
    top: 196px;
    width: 340px;
    height: 595px;
    overflow: hidden;
    box-shadow: 0 10px 30px rgba(0,0,0,.45);
  }
  .card--front { left: 215px; background: var(--yellow); }
  .card--back { left: 645px; background: var(--yellow); }

  /* front */
  .front-brand {
    height: 255px;
    background: var(--white);
    border-bottom: 5px solid var(--black);
    display: flex;
    align-items: center;
    justify-content: center;
    gap: 14px;
  }
  .brand-dot { width: 22px; height: 22px; border-radius: 50%; background: var(--black); }
  .brand-name {
    font-family: var(--display);
    font-weight: 800;
    font-size: 30px;
    color: var(--black);
    letter-spacing: 1px;
  }
  .front-info { text-align: center; padding-top: 56px; }
  .owner-name {
    font-family: var(--display);
    font-weight: 800;
    font-size: 21px;
    letter-spacing: 1.5px;
    text-transform: uppercase;
  }
  .owner-role { font-size: 14px; margin-top: 8px; text-transform: uppercase; }
  .address { font-size: 16px; line-height: 1.3; margin-top: 18px; }
  .contacts { list-style: none; margin-top: 18px; font-size: 16px; line-height: 1.35; }
  .contacts li { display: flex; align-items: center; justify-content: center; gap: 7px; }
  .contacts svg { width: 13px; height: 13px; fill: var(--ink); }

  /* back */
  .tagline {
    font-family: var(--display);
    font-weight: 800;
    font-size: 19px;
    line-height: 1.3;
    letter-spacing: 1.5px;
    text-align: center;
    text-transform: uppercase;
    padding-top: 58px;
  }
  .back-brand {
    position: absolute;
    top: 240px; left: 0; right: 0;
    text-align: center;
  }
  .back-brand .brand-name { font-size: 36px; }
  .social-band {
    position: absolute;
    left: 0; right: 0;
    top: 452px;
    height: 66px;
    background: var(--black);
    display: flex;
    align-items: center;
    justify-content: center;
    gap: 12px;
  }
  .social-dot { width: 20px; height: 20px; border-radius: 50%; background: var(--yellow); }
  .social-handle { color: var(--white); font-size: 18px; font-weight: 500; }
</style>
</head>
<body>

<section class="card card--front">
  <div class="front-brand">
    <span class="brand-dot"></span>
    <span class="brand-name">QPKZ Comics</span>
  </div>
  <div class="front-info">
    <h1 class="owner-name">Elias Moreno</h1>
    <p class="owner-role">Owner</p>
    <p class="address">PO Box 617283<br>Miami, FL 33827</p>
    <ul class="contacts">
      <li><svg viewBox="0 0 24 24"><path d="M6.6 10.8a15.1 15.1 0 0 0 6.6 6.6l2.2-2.2c.3-.3.7-.4 1-.2 1.1.4 2.3.6 3.6.6.6 0 1 .4 1 1V20c0 .6-.4 1-1 1A17 17 0 0 1 3 4c0-.6.4-1 1-1h3.5c.6 0 1 .4 1 1 0 1.2.2 2.4.6 3.6.1.3 0 .7-.2 1z"/></svg>305-482-6170</li>
      <li><svg viewBox="0 0 24 24"><path d="M2 5h20v14H2zm2 2v.5l8 5 8-5V7z"/></svg>hello@qpkzmail.com</li>
      <li><svg viewBox="0 0 24 24"><circle cx="12" cy="12" r="10"/></svg>www.qpkzshop.com</li>
    </ul>
  </div>
</section>

<section class="card card--back">
  <h2 class="tagline">Buy &amp; Sell Comics<br>&amp; Collectables</h2>
  <div class="back-brand"><span class="brand-name">QPKZ Comics</span></div>
  <div class="social-band">
    <span class="social-dot"></span>
    <span class="social-handle">QPKZ.Comics</span>
  </div>
</section>

</body>
</html>
```